real esate business card with company logo and name

we need a business card design for a real esate company

The company name is Walsh & Brand Pty Ltd, and we have our logo designed and will upload. We want classic or moden feel. Black or white background. looks more textured. Should include folowinginformations
Owen Walsh and Lucy Brand
Sales Agents & Onsite Manager
p: 07 5948 2063
F: 07 5948 2174
M:0431 857 219
3/42 Marlow Crescent, FERNLEA QLD 4213

We want this business card looks professonal. Thank you in advance.

Industry/Entity Type

Real Estate Agent

Contact Information for Business Card

Owen Walsh and Lucy Brand
Onsite Manager & Sales Agents
p: 07 5948 2063
M:0431 857 219

Font styles to use
Serif

Colors
000000
fbfbfb
333333
959595

Requirements
Must have
• company logo and name, black or white back ground

```html
<!DOCTYPE html>
<html lang="en">
<head>
<meta charset="utf-8">
<title>Walsh &amp; Brand Pty Ltd — Business Card</title>
<link href="https://fonts.googleapis.com/css2?family=Michroma&family=Open+Sans:wght@400;600&display=swap" rel="stylesheet">
<style>
  :root {
    --bg: #d9d9d9;
    --card-dark: #595959;
    --card-dark-edge: #4a4a4a;
    --card-light: #fbfbfb;
    --ink: #000000;
    --ink-soft: #333333;
    --grey: #959595;
    --grey-mid: #7a7a7a;
    --white: #ffffff;
  }
  * { margin: 0; padding: 0; box-sizing: border-box; }
  html, body { width: 1200px; height: 864px; overflow: hidden; }
  body { background: var(--bg); position: relative; font-family: "Open Sans", Arial, sans-serif; }

  .card { position: absolute; width: 540px; height: 330px; box-shadow: 0 6px 18px rgba(0,0,0,.25); overflow: hidden; }

  .card--back {
    left: 150px; top: 80px;
    background: linear-gradient(135deg, #636363 0%, var(--card-dark) 55%, var(--card-dark-edge) 100%);
    display: flex; align-items: center; justify-content: center;
  }
  .card--back .company-name { color: var(--white); font-size: 21px; letter-spacing: 1px; }

  .card--front {
    left: 510px; top: 454px;
    background: radial-gradient(circle at 35% 30%, var(--white) 0%, var(--card-light) 50%, #ececec 100%);
  }

  .company-name { font-family: "Michroma", Arial, sans-serif; text-transform: uppercase; white-space: nowrap; }

  .brand { position: absolute; right: 26px; top: 30px; display: flex; flex-direction: column; align-items: center; gap: 14px; }
  .brand-square { width: 80px; height: 80px; background: var(--grey-mid); }
  .card--front .company-name { color: var(--ink-soft); font-size: 11.5px; letter-spacing: .3px; line-height: 16px; }

  .people { position: absolute; left: 32px; top: 150px; }
  .people-names { color: var(--grey-mid); font-weight: 600; font-size: 17px; line-height: 24px; white-space: nowrap; }
  .people-role { color: var(--ink); font-size: 13px; line-height: 18px; white-space: nowrap; }

  .divider { position: absolute; left: 240px; right: 26px; top: 206px; height: 1px; background: var(--grey); }

  .contact { position: absolute; right: 28px; top: 224px; text-align: right; color: var(--ink); font-size: 14px; line-height: 20px; }
  .contact-line { display: flex; justify-content: flex-end; align-items: center; gap: 8px; }
  .contact-line svg { width: 13px; height: 13px; fill: none; stroke: var(--ink-soft); stroke-width: 1.4; }
  .contact-address { margin-top: 6px; font-size: 14.5px; white-space: nowrap; }
</style>
</head>
<body>
  <section class="card card--back">
    <span class="company-name">Walsh &amp; Brand Pty Ltd.</span>
  </section>

  <section class="card card--front">
    <div class="brand">
      <span class="brand-square" aria-hidden="true"></span>
      <span class="company-name">Walsh &amp; Brand Pty Ltd.</span>
    </div>

    <div class="people">
      <p class="people-names">Owen Walsh and Lucy Brand</p>
      <p class="people-role">Onsite Manager &amp; Sales Agents</p>
    </div>

    <div class="divider"></div>

    <div class="contact">
      <p class="contact-line">07 5948 2063
        <svg viewBox="0 0 16 16" aria-label="phone"><path d="M2 5c0-2 2-3 6-3s6 1 6 3l-2 1-1-2H5L4 6 2 5z"/><path d="M4 8h8l1 6H3l1-6z"/></svg>
      </p>
      <p class="contact-line">0431 857 219
        <svg viewBox="0 0 16 16" aria-label="mobile"><rect x="4.5" y="1.5" width="7" height="13" rx="1.2"/><line x1="7" y1="12.5" x2="9" y2="12.5"/></svg>
      </p>
      <p class="contact-address">3/42 Marlow Crescent FERNLEA QLD 4213</p>
    </div>
  </section>
</body>
</html>
```